Website Design - TallyPorchHelpers.net

PLEASE CHECK WORD DOCUMENT ATTACHED FOR WEBSITE FLOW.

Target Market(s)

REAL ESTATE AGENTS ARE THE TARGET MARKET

Industry/Entity Type

Real Estate

Coding

Coded - Design and coding required

Number of Pages Required

4 page

Colors

Designer to choose colors to be used in the design.

Requirements
Must have
• WE LIKE RED LOGO ATTACHED
Nice to have
• PLEASE CHECK WORD DOCUMENT ATTACHED FOR WEBSITE FLOW.
Should not have

```html
<!DOCTYPE html>
<html lang="en">
<head>
<meta charset="utf-8">
<title>TallyPorchHelpers.net</title>
<link rel="stylesheet" href="https://fonts.googleapis.com/css2?family=Open+Sans:ital,wght@0,400;0,600;0,700;0,800;1,400&display=swap">
<style>
:root{
  --red:#e3051b;
  --navy:#221d7e;
  --dark:#2b2b2b;
  --darker:#232323;
  --grey:#f1f1f1;
  --text:#333;
  --muted:#777;
  --white:#fff;
}
*{box-sizing:border-box;margin:0;padding:0}
html,body{width:1200px;height:3689px;overflow:hidden;background:var(--white)}
body{font-family:"Open Sans",Arial,sans-serif;color:var(--text);position:relative}
.band{position:absolute;left:0;width:1200px}
.center{text-align:center}
.section-title{font-weight:700;font-size:24px;color:var(--red);text-align:center;letter-spacing:.3px}
.section-title.navy{color:var(--navy)}

/* header */
.site-header{top:0;height:91px}
.brand{position:absolute;left:135px;top:30px;display:flex;align-items:center;gap:8px}
.brand-square{width:22px;height:22px;background:var(--red)}
.brand-name{font-weight:800;font-size:19px;color:var(--red)}
.main-nav{position:absolute;left:349px;top:36px;display:flex;gap:24px;font-size:12px}
.main-nav a{color:var(--navy);text-decoration:none}
.main-nav a.active{color:var(--red)}
.call{position:absolute;left:688px;top:18px;text-align:right;width:114px;line-height:1.25}
.call small{display:block;font-size:12px;color:#222}
.call strong{display:block;font-size:14px;color:var(--red);font-weight:700}
.call-icon{position:absolute;left:812px;top:28px;width:34px;height:34px;border-radius:50%;background:var(--red)}
.newsletter{position:absolute;left:866px;top:22px;width:201px;height:44px;border:1px solid #bbb;display:flex;align-items:center;justify-content:space-between;padding:0 12px;font-size:10px;color:#666}

/* hero */
.hero{top:91px;height:524px;background:linear-gradient(180deg,#9aa8b7 0%,#c9ced3 35%,#6f8a5a 70%,#4f7a33 100%)}
.hero-name{position:absolute;left:190px;top:170px;font-weight:800;font-size:46px;color:var(--white);line-height:1.1;width:340px}
.slide-arrow{position:absolute;top:252px;width:22px;height:22px;background:#222;border-radius:3px}
.slide-arrow.prev{left:4px}.slide-arrow.next{right:4px}
.tagline{position:absolute;left:135px;top:438px;width:930px;height:86px;background:var(--navy);color:var(--white);text-align:center;padding-top:15px}
.tagline h1{font-size:24px;font-weight:700;letter-spacing:.3px}
.tagline p{font-size:15px;margin-top:2px}

/* chooser */
.chooser{position:absolute;left:133px;top:615px;width:934px;height:214px;background:var(--dark)}
.chooser h2{color:var(--white);font-size:22px;font-weight:700;text-align:center;margin-top:26px;letter-spacing:.3px}
.options{position:absolute;left:15px;top:74px;display:flex;gap:10px}
.option{width:295px;height:123px;border:1px solid #888;text-align:center;color:var(--white);padding-top:22px}
.option svg{display:block;margin:0 auto 8px}
.option b{display:block;font-size:14px;font-weight:700}
.option span{display:block;font-size:10px;margin-top:3px}

/* about & services */
.about{top:890px}
.about h2{color:var(--navy);font-size:24px;font-weight:700;text-align:center}
.about p{text-align:center;font-size:15px;margin-top:4px}
.trio{position:absolute;left:0;width:1200px}
.trio-item{position:absolute;width:240px;text-align:center;margin-left:-120px}
.disc{width:118px;height:118px;border-radius:50%;background:var(--red);margin:0 auto;display:flex;align-items:center;justify-content:center}
.trio-item b{display:block;font-size:14px;font-weight:700;margin-top:18px;color:#222}

/* packages */
.packages{top:1259px;height:581px;background:var(--grey)}
.cards{position:absolute;left:133px;top:132px;display:flex;gap:17px}
.card{width:173px;position:relative}
.card-badge{height:58px;text-align:center;font-size:11px;font-weight:800;color:var(--red);padding-top:30px}
.card-body{height:312px;background:var(--navy);border:2px solid #140f5c;color:var(--white);padding:14px 10px 0}
.card-body h3{text-align:center;font-size:21px;font-weight:700}
.price{text-align:center;font-size:24px;font-weight:700;margin-top:8px;height:40px}
.price.custom{font-size:11px;line-height:1.3;margin-top:8px;height:40px}
.card-body ol{list-style:none;font-size:9.5px;line-height:1.35;margin-top:10px}
.card-body li{margin-bottom:9px}
.buy{position:absolute;left:14px;right:14px;bottom:16px;height:44px;background:var(--white);color:#111;font-size:15px;font-weight:600;display:flex;align-items:center;justify-content:center}

/* how it works */
.how{top:1900px;height:240px}
.how-line{position:absolute;top:119px;left:278px;width:642px;height:2px;background:var(--red)}

/* add-ons */
.addons{top:2184px;height:586px;background:var(--grey)}
.addons h2{color:var(--navy);font-size:24px;font-weight:700;text-align:center;margin-top:80px}
.addons > p{text-align:center;font-size:15px}
.addon-panel{position:absolute;left:133px;top:146px;width:934px;height:359px;display:flex}
.addon-list{width:467px;background:var(--navy);color:var(--white);padding:40px 0 0 20px}
.addon{display:flex;gap:14px;margin-bottom:22px}
.addon svg{flex:none;margin-top:2px}
.addon h4{font-size:17px;font-weight:700}
.addon p{font-size:10px;line-height:1.4;max-width:390px}
.addon-photo{width:467px;background:linear-gradient(180deg,#3f82d8 0%,#9cc4ec 40%,#8e8f86 60%,#4f8a2d 100%)}
.signup{position:absolute;left:388px;top:337px;width:158px;height:44px;background:var(--white);box-shadow:0 2px 6px rgba(0,0,0,.25);font-size:14px;font-weight:600;display:flex;align-items:center;justify-content:center;color:#111}

/* testimonials */
.testimonials{top:2836px}
.testimonials h2{color:var(--navy);font-size:24px;font-weight:700;text-align:center}
.quote{width:760px;margin:14px auto 0;text-align:center;font-size:16px;line-height:1.5;color:#333}
.cite{text-align:center;color:var(--red);font-size:16px;margin-top:10px}
.dots{display:flex;justify-content:center;gap:12px;margin-top:14px}
.dots i{width:11px;height:11px;border-radius:50%;background:#bbb}
.dots i.on{background:var(--navy)}

/* faq */
.faq{top:3072px;height:318px;background:var(--grey);text-align:center}
.faq h2{color:var(--navy);font-size:24px;font-weight:700;margin-top:74px}
.faq h3{font-size:17px;font-weight:400;margin-top:4px;color:#222}
.faq p{width:930px;margin:6px auto 0;font-size:10px;line-height:1.6;color:#555}
.view-all{display:inline-block;margin-top:18px;width:84px;height:32px;line-height:30px;border:1px solid #bbb;font-size:10px;color:#555;background:#fafafa}

/* footer */
.site-footer{top:3390px;height:299px;background:var(--dark);color:#ccc}
.foot-brand{position:absolute;left:135px;top:50px;display:flex;align-items:center;gap:8px}
.foot-brand .brand-square{background:#bbb;width:20px;height:20px}
.foot-brand span{font-weight:800;font-size:17px;color:#ddd}
.foot-col{position:absolute;top:30px}
.foot-col h5{font-size:18px;font-weight:600;color:var(--white);margin-bottom:14px}
.foot-col a{display:block;font-size:10px;color:#bbb;text-decoration:none;margin-bottom:12px}
.social a{display:flex;align-items:center;gap:14px;margin-bottom:26px}
.social i{width:14px;height:14px;background:#bbb;border-radius:50%}
.foot-rule{position:absolute;left:133px;top:226px;width:934px;height:1px;background:#444}
.copyright{position:absolute;top:252px;width:1200px;text-align:center;font-size:10px;color:#aaa}
</style>
</head>
<body>

<header class="band site-header">
  <div class="brand"><span class="brand-square"></span><span class="brand-name">TallyPorchHelpers</span></div>
  <nav class="main-nav">
    <a class="active" href="#">Services</a><a href="#">Packages</a><a href="#">How it Works</a><a href="#">About us</a><a href="#">FAQ</a>
  </nav>
  <div class="call"><small>Call Or Text Us</small><strong>1-555-014-2290</strong><strong>1 800 555 0148</strong></div>
  <div class="call-icon">
    <svg width="34" height="34" viewBox="0 0 34 34"><path d="M12 9c1 0 2 3 2 4s-2 1-1 3 2 3 4 4 2-1 3-1 4 1 4 2-1 3-3 3c-6 0-12-6-12-12 0-2 2-3 3-3z" fill="#fff"/></svg>
  </div>
  <div class="newsletter"><span>Subscribe To Our Newsletter</span>
    <svg width="14" height="10" viewBox="0 0 14 10"><rect width="14" height="10" fill="#555"/><path d="M0 0l7 5 7-5" stroke="#fff" fill="none"/></svg>
  </div>
</header>

<section class="band hero" role="img" aria-label="Photo of a grey suburban house with a front lawn, porch and shrubs">
  <div class="hero-name">TallyPorchHelpers</div>
  <span class="slide-arrow prev"><svg width="22" height="22" viewBox="0 0 22 22"><path d="M13 6l-5 5 5 5" stroke="#fff" stroke-width="2" fill="none"/></svg></span>
  <span class="slide-arrow next"><svg width="22" height="22" viewBox="0 0 22 22"><path d="M9 6l5 5-5 5" stroke="#fff" stroke-width="2" fill="none"/></svg></span>
  <div class="tagline">
    <h1>HELPING AGENTS SAVE TIME AND MONEY.</h1>
    <p>We place signs and boost foot traffic to your open houses using proven marketing techniques.</p>
  </div>
</section>

<section class="chooser">
  <h2>CHOOSE THE OPTION BELOW THAT BEST DESCRIBES YOU</h2>
  <div class="options">
    <div class="option">
      <svg width="32" height="32" viewBox="0 0 32 32"><circle cx="16" cy="10" r="7" fill="#fff"/><path d="M3 30c0-8 6-12 13-12s13 4 13 12z" fill="#fff"/></svg>
      <b>I'M A FULL ON BROKERAGE</b><span>LEAD FORM POP UP</span>
    </div>
    <div class="option">
      <svg width="46" height="32" viewBox="0 0 46 32"><circle cx="23" cy="9" r="6" fill="#fff"/><circle cx="9" cy="12" r="4.5" fill="#fff"/><circle cx="37" cy="12" r="4.5" fill="#fff"/><path d="M13 30c0-7 4-11 10-11s10 4 10 11z" fill="#fff"/><path d="M1 28c0-6 3-9 8-9 2 0 3 .5 4 1-2 2-3 5-3 8z" fill="#fff"/><path d="M45 28c0-6-3-9-8-9-2 0-3 .5-4 1 2 2 3 5 3 8z" fill="#fff"/></svg>
      <b>I'M AN IND. BROKER WITH A TEAM</b><span>LEAD FORM POP UP</span>
    </div>
    <div class="option">
      <svg width="32" height="32" viewBox="0 0 32 32"><rect x="3" y="7" width="22" height="22" fill="none" stroke="#fff" stroke-width="3"/><path d="M14 19l14-14 3 3-14 14-4 1z" fill="#fff"/></svg>
      <b>I NEED SIGN PLACEMENT ASAP</b><span>GOES TO PACKAGES TO BUY NOW</span>
    </div>
  </div>
</section>

<section class="band about">
  <h2>ABOUT TALLYPORCHHELPERS</h2>
  <p>Helping agents leverage their time and skills to increase production at an affordable price with impeccable support.</p>
  <h2 class="section-title" style="margin-top:28px">SERVICES</h2>
  <div class="trio" style="top:141px">
    <div class="trio-item" style="left:278px"><div class="disc">
      <svg width="56" height="56" viewBox="0 0 56 56" fill="none" stroke="#fff" stroke-width="2.5"><path d="M10 8h36M16 8v8M40 8v8"/><rect x="10" y="16" width="36" height="24"/><path d="M20 34v-8l8-6 8 6v8z"/><path d="M28 40v10"/></svg>
    </div><b>SIGN BOARDS</b></div>
    <div class="trio-item" style="left:600px"><div class="disc">
      <svg width="56" height="56" viewBox="0 0 56 56" fill="none" stroke="#fff" stroke-width="2.5"><path d="M12 30l22-14v28L12 34z"/><path d="M16 34l3 12h5l-3-11"/><path d="M40 22l6-4M41 30h7M40 38l6 4"/></svg>
    </div><b>INCREASE MARKETING</b></div>
    <div class="trio-item" style="left:920px"><div class="disc">
      <svg width="56" height="56" viewBox="0 0 56 56" fill="none" stroke="#fff" stroke-width="2.5"><rect x="12" y="8" width="28" height="38"/><rect x="18" y="14" width="16" height="12"/><path d="M18 32h16M18 38h10"/><circle cx="40" cy="40" r="7" fill="#e3051b"/></svg>
    </div><b>EASY ADVERTISMENTS</b></div>
  </div>
</section>

<section class="band packages">
  <h2 class="section-title" style="margin-top:70px">PACKAGES</h2>
  <div class="cards">
    <div class="card"><div class="card-badge">TallyPorchHelpers</div><div class="card-body">
      <h3>5 SIGNS</h3><div class="price">$49</div>
      <ol><li>1. Place signs strategically in best areas according to where the open house is located</li><li>2. Pick Up the signs after the open house</li><li>3. Store custom signs for you if needed</li></ol>
      <div class="buy">BUY NOW</div></div></div>
    <div class="card"><div class="card-badge">TallyPorchHelpers</div><div class="card-body">
      <h3>10 SIGNS</h3><div class="price">$59</div>
      <ol><li>1. Place signs strategically in best areas according to where the open house is located</li><li>2. Pick Up the signs after the open house</li><li>3. Store custom signs for you if needed</li></ol>
      <div class="buy">BUY NOW</div></div></div>
    <div class="card"><div class="card-badge">TallyPorchHelpers</div><div class="card-body">
      <h3>15 SIGNS</h3><div class="price">$69</div>
      <ol><li>1. Place signs strategically in best areas according to where the open house is located</li><li>2. Pick Up the signs after the open house</li><li>3. Store custom signs for you if needed</li></ol>
      <div class="buy">BUY NOW</div></div></div>
    <div class="card"><div class="card-badge">TallyPorchHelpers</div><div class="card-body">
      <h3>20 SIGNS</h3><div class="price">$79</div>
      <ol><li>1. Place signs strategically in best areas according to where the open house is located</li><li>2. Pick Up the signs after the open house</li><li>3. Store custom signs for you if needed</li></ol>
      <div class="buy">BUY NOW</div></div></div>
    <div class="card"><div class="card-badge">TallyPorchHelpers</div><div class="card-body">
      <h3>25+ SIGNS</h3><div class="price custom">CLICK BUY NOW TO<br>CREATE CUSTOM PKG</div>
      <ol><li>1. Place signs strategically in best areas according to where the open house is located</li><li>2. Pick Up the signs after the open house</li><li>3. Store custom signs for you if needed</li></ol>
      <div class="buy">BUY NOW</div></div></div>
  </div>
</section>

<section class="band how">
  <h2 class="section-title" style="margin-top:16px">HOW IT WORKS</h2>
  <div class="how-line"></div>
  <div class="trio" style="top:61px">
    <div class="trio-item" style="left:278px"><div class="disc">
      <svg width="56" height="56" viewBox="0 0 56 56" fill="none" stroke="#fff" stroke-width="2.5"><rect x="18" y="8" width="20" height="38"/><path d="M22 14h4M30 14h4M22 22h4M30 22h4M22 30h4M30 30h4M12 46h32"/></svg>
    </div><b>CHOOSE BROKER OR HOUSE OWNER</b></div>
    <div class="trio-item" style="left:600px"><div class="disc">
      <svg width="56" height="56" viewBox="0 0 56 56" fill="none" stroke="#fff" stroke-width="2.5"><path d="M10 26l18-16 18 16"/><path d="M15 22v24h26V22"/><rect x="20" y="28" width="16" height="8"/></svg>
    </div><b>CHOOSE SIGN BOARD</b></div>
    <div class="trio-item" style="left:920px"><div class="disc">
      <svg width="56" height="56" viewBox="0 0 56 56" fill="none" stroke="#fff" stroke-width="2.5"><path d="M14 8v40M14 14h28M20 14v4M36 14v4"/><rect x="18" y="18" width="22" height="16"/><path d="M22 26h14"/></svg>
    </div><b>PLACE SIGN BOARD</b></div>
  </div>
</section>

<section class="band addons">
  <h2>ADD ON MARKETING SERVICES</h2>
  <p>Sign up for a subscription and get these marketing services for free</p>
  <div class="addon-panel">
    <div class="addon-list">
      <div class="addon"><svg width="34" height="30" viewBox="0 0 34 30"><path d="M17 3C8 3 2 8 2 14c0 3 2 6 5 8l-2 6 7-4c2 .5 3 .5 5 .5 9 0 15-5 15-10.5S26 3 17 3z" fill="#fff"/></svg>
        <div><h4>SMS</h4><p>SMS Send sms blast to your neighborhood informing them your home is for sale and if they know anyone looking to send them over</p></div></div>
      <div class="addon"><svg width="34" height="30" viewBox="0 0 34 30"><rect x="3" y="6" width="28" height="19" fill="#fff"/><path d="M3 6l14 11 14-11" stroke="#221d7e" stroke-width="2" fill="none"/></svg>
        <div><h4>EMAIL</h4><p>Email blast to your neighborhood informing them your home is for sale and if they know anyone looking to send them over</p></div></div>
      <div class="addon"><svg width="34" height="30" viewBox="0 0 34 30"><circle cx="17" cy="15" r="10" fill="#fff"/></svg>
        <div><h4>SOCIAL AD</h4><p>Newsfeed ads to people in your open house area</p></div></div>
      <div class="addon"><svg width="34" height="30" viewBox="0 0 34 30"><rect x="4" y="5" width="26" height="20" fill="none" stroke="#fff" stroke-width="3"/><path d="M6 23l8-9 6 6 4-4 5 7z" fill="#fff"/></svg>
        <div><h4>VB</h4><p>VB blast to your neighborhood informing them your home is for sale and if they know anyone looking to send them over</p></div></div>
    </div>
    <div class="addon-photo" role="img" aria-label="Photo of a blue two-storey house with a green lawn under a clear sky"></div>
    <div class="signup">SIGN UP NOW</div>
  </div>
</section>

<section class="band testimonials">
  <h2>TESTIMONIALS</h2>
  <p class="quote">" Etiam mattis augue vehicula odio posuere, sit amet tempus lectus luctus. Nulla facilisi. Etiam vel massa elementum, bibendum tellus venenatis, feugiat massa. Curabitur venenatis lacinia ornare. "</p>
  <p class="cite">Dana Reyes, City</p>
  <div class="dots"><i class="on"></i><i></i><i></i><i></i></div>
</section>

<section class="band faq">
  <h2>FAQ</h2>
  <h3>Pellentesque convallis molestie enim sit amet efficitur?</h3>
  <p>Agents can book sign placement for any open house in our service area. Signs go out the morning of the event and are collected after close. Custom signs are stored at no extra cost until your next listing is ready to show.</p>
  <span class="view-all">View All</span>
</section>

<footer class="band site-footer">
  <div class="foot-brand"><span class="brand-square"></span><span>TallyPorchHelpers</span></div>
  <div class="foot-col" style="left:580px">
    <h5>Links</h5>
    <a href="#">Service</a><a href="#">Packages</a><a href="#">How it works</a><a href="#">About us</a><a href="#">FAQ</a>
  </div>
  <div class="foot-col social" style="left:954px">
    <h5>Follow us on</h5>
    <a href="#"><i></i>Social Page</a><a href="#"><i></i>Microblog</a><a href="#"><i></i>Video Channel</a>
  </div>
  <div class="foot-rule"></div>
  <p class="copyright">Copyright © 2018 TallyPorchHelpers. All rights reserved.</p>
</footer>

</body>
</html>
```